Bright Harbor Design

We need a web design for our startup company based in Zurich, Switzerland called Bright Harbor. We offer professional flirt and dating advice, self development with seminars and practical coachings.

The final website aims for two capital goals. First, it will contain text, pictures and video based content presenting and advertising our services. Furthermore, we want to bind our costumers with a plattform offering them to share their expiriences related with our services.

The targeted group will be men from 25 to 40 years.
Updates

The design requires also a register-box to put in the clients Name and Email

I need (besides of the "email registration box") a "Video Gallery", "Blog" and "Agenda (with the next events to come)"

Reason: I want to make a poll now

Target Market(s)

Guys around 25 to 40 years who want to improve their social lifestyle

Industry/Entity Type

Advertising

Requirements
Must have
• First and foremost, the design must transfer strong emotions and suggest an attractive social lifestyle.

The design should not be overloaded with content but should include pictures, videos and text.

The design should present a modern, urban lifestyle.
Nice to have
• There is a logo attached to the assignement. However, if you have a good idea for an improved or different logo, please do not hesitate to design your ideas.

```html
<!DOCTYPE html>
<html lang="en">
<head>
<meta charset="utf-8">
<title>Bright Harbor – Dating &amp; Flirting Advice</title>
<link href="https://fonts.googleapis.com/css2?family=Ubuntu:ital,wght@0,400;0,500;0,700;1,400&display=swap" rel="stylesheet">
<style>
:root{
  --navy:#1d2f5a;
  --blue:#1d7dc2;
  --sky:#1ba6dd;
  --sky-dark:#1591c9;
  --nav-top:#4fb4ea;
  --nav-bot:#1e8fd2;
  --footer:#3a9fd9;
  --orange:#ff8a00;
  --orange-dark:#f06f00;
  --green:#4fae1c;
  --text:#4a4a4a;
  --muted:#666;
  --panel:#ececec;
  --white:#fff;
}
*{box-sizing:border-box;margin:0;padding:0}
html,body{width:1000px;height:1200px;overflow:hidden}
body{font-family:'Ubuntu',sans-serif;background:var(--white);position:relative;color:var(--text)}
.abs{position:absolute}

/* header */
.site-header{left:0;top:0;width:1000px;height:98px;background:linear-gradient(#fff,#f1f1f1)}
.brand{left:111px;top:30px;display:flex;align-items:center;gap:10px;font-size:30px;font-weight:700;color:var(--navy)}
.brand-dot{width:22px;height:22px;border-radius:50%;background:var(--navy)}
.main-nav{left:442px;top:55px;width:450px;height:32px;border-radius:16px;background:linear-gradient(var(--nav-top),var(--nav-bot));display:flex;align-items:center;justify-content:center;font-size:11.5px;color:#fff}
.main-nav span{padding:0 8px}
.main-nav .sep{padding:0 4px;opacity:.9}

/* hero */
.hero-band{left:0;top:98px;width:1000px;height:371px;background:radial-gradient(circle at 900px 150px,var(--sky) 0,var(--sky-dark) 60%,#1c9fd9 100%)}
.slider{left:108px;top:126px;width:784px;height:301px;background:#fff;border:1px solid #d5d5d5;box-shadow:0 14px 16px -8px rgba(0,40,80,.45)}
.slide-photo{left:4px;top:4px;width:560px;height:292px;background:linear-gradient(90deg,#4d4e52 0%,#7e8288 45%,#b9bcc0 72%,rgba(255,255,255,0) 100%)}
.slide-copy{left:500px;top:52px;width:270px}
.slide-copy .pre{font-size:25px;font-weight:500;color:#555;line-height:30px}
.slide-copy .name{font-size:29px;font-weight:500;color:var(--blue);line-height:34px}
.slide-copy .tag{font-size:16.5px;font-weight:500;color:#444;margin-top:4px}
.slide-copy .lead{font-size:12.5px;font-style:italic;color:#555;line-height:21px;margin-top:9px}
.btn-orange{background:linear-gradient(#ffa020,var(--orange-dark));color:#fff;font-weight:500;border-radius:3px;display:flex;align-items:center;justify-content:center}
.cta{left:500px;top:221px;width:119px;height:28px;font-size:14.5px;box-shadow:0 2px 3px rgba(0,0,0,.25)}
.dots{left:683px;top:271px;display:flex;gap:4px}
.dots i{width:16px;height:16px;border-radius:50%;background:#999}
.dots i:first-child{background:#333}

/* welcome */
.welcome-photo{left:112px;top:497px;width:180px;height:182px;border-radius:40%;background:radial-gradient(ellipse at 55% 45%,#c89070 0%,#d9b59c 45%,rgba(255,255,255,0) 72%)}
.welcome{left:308px;top:499px;width:370px}
.welcome h1{font-size:20px;font-weight:500;color:var(--blue);margin-bottom:9px}
.welcome p{font-size:10.4px;line-height:19.2px;color:var(--text)}
.read-more{left:308px;top:676px;width:77px;height:26px;font-size:12px}

/* services */
.services{left:708px;top:502px;width:184px;height:231px;background:#f0f0f0}
.services h2{height:27px;background:linear-gradient(var(--nav-top),var(--nav-bot));color:#fff;font-size:16px;font-weight:400;padding:3px 10px}
.services ul{list-style:none;padding:8px 0 0 11px}
.services li{height:24.2px;font-size:10px;color:#333;display:flex;align-items:center;gap:12px}

/* panels */
.panel{top:749px;width:250px;height:233px;background:linear-gradient(#e6e6e6,#f3f3f3 60%,#e8e8e8);border-radius:3px;box-shadow:0 8px 8px -7px rgba(0,0,0,.45)}
.panel h2{position:absolute;left:15px;top:8px;font-size:20px;font-weight:500;color:var(--blue)}
.thumb{position:absolute;width:101px;height:71px;border:3px solid #fff;box-shadow:0 1px 3px rgba(0,0,0,.3)}
.play{position:absolute;left:50%;top:50%;transform:translate(-50%,-50%)}
.post{position:absolute;left:15px;width:225px}
.post .pic{position:absolute;left:0;top:0;width:71px;height:71px;border:3px solid #fff;box-shadow:0 1px 3px rgba(0,0,0,.3)}
.post h3{position:absolute;left:82px;top:0;font-size:12px;font-weight:500;color:var(--orange);white-space:nowrap}
.post p{position:absolute;left:82px;top:17px;width:140px;font-size:10px;line-height:15px;color:var(--muted)}
.post p em{color:var(--blue)}
.post-rule{position:absolute;left:16px;top:122px;width:218px;height:1px;background:#cfcfcf}

/* register */
.register{left:108px;top:1008px;width:784px;height:70px;border:1px solid #cfcfcf;border-radius:3px;background:linear-gradient(#fafafa,#efefef);box-shadow:0 2px 2px rgba(0,0,0,.12)}
.register label{position:absolute;left:23px;top:22px;font-size:18.5px;font-weight:500;color:var(--blue)}
.register .field{position:absolute;left:216px;top:18px;width:393px;height:30px;background:#fff;border:1px solid #ddd;border-radius:3px;font-size:11.5px;color:#aaa;padding:7px 12px}
.register .go{position:absolute;left:625px;top:18px;width:125px;height:31px;background:linear-gradient(#6cc12b,var(--green));border:1px solid #3b8d10;border-radius:3px;color:#fff;font-size:14.5px;font-weight:500;display:flex;align-items:center;justify-content:center}

/* footer */
.site-footer{left:0;top:1101px;width:1000px;height:99px;background:var(--footer);color:#fff}
.foot-nav{position:absolute;left:108px;top:25px;font-size:10.5px;display:flex}
.foot-nav span{margin-right:15px}
.foot-nav .sep{margin-right:15px}
.copy{position:absolute;left:108px;top:58px;font-size:9.5px}
.copy b{font-weight:400;color:#bfe6ff}
.follow{position:absolute;left:653px;top:21px;font-size:11.5px;font-weight:500}
.social{position:absolute;left:651px;top:41px;display:flex;gap:8.5px}
.social i{width:33px;height:33px;border-radius:50%;border:3px solid #fff;box-shadow:0 1px 2px rgba(0,0,0,.3)}
</style>
</head>
<body>

<header class="site-header abs">
  <div class="brand abs"><span class="brand-dot"></span>Bright Harbor</div>
  <nav class="main-nav abs">
    <span>Home</span><span class="sep">|</span><span>About Us</span><span class="sep">|</span><span>Services</span><span class="sep">|</span><span>Videos</span><span class="sep">|</span><span>Gallery</span><span class="sep">|</span><span>Contact Us</span>
  </nav>
</header>

<section class="hero-band abs">
  <div class="slider abs" style="top:28px">
    <div class="slide-photo abs" role="img" aria-label="Man and woman chatting on a city street"></div>
    <div class="slide-copy abs">
      <div class="pre">Welcome to</div>
      <div class="name">BRIGHT HARBOR</div>
      <div class="tag">A Dating &amp; Flirting Advise Site...</div>
      <p class="lead">Lorem ipsum dolor sit amet, consectetur adipi-scing elit. Fusce accumsan, elit a suscipit sag-ittis, tortor sapien cursus risus.</p>
    </div>
    <div class="btn-orange cta abs">Get Connected</div>
    <div class="dots abs"><i></i><i></i><i></i><i></i></div>
  </div>
</section>

<div class="welcome-photo abs" role="img" aria-label="Smiling young couple embracing"></div>
<article class="welcome abs">
  <h1>Welcome to Our Site</h1>
  <p>Aliquam molestie, mi et imperdiet euismod, dui purus auctor tellus, et inter-dum lacus lectus et ante. Sed accumsan sollicitudin sapien, sit amet adipi-scing turpis gravida ac. In congue, neque ac lobortis volutpat, libero mauris varius mi, vitae suscipit ipsum ligula vitae risus. Duis aliquam nibh a dui iaculis viverra id a velit. Vivamus egestas risus in magna varius commodo. Sed semper viverra egestas. Etiam pretium porttitor lectus, vel ornare neque porta volutpat.</p>
</article>
<div class="btn-orange read-more abs">Read More</div>

<aside class="services abs">
  <h2>Our Services</h2>
  <ul>
    <li><svg width="9" height="9" viewBox="0 0 10 10"><path d="M5 9 1 5a2.2 2.2 0 0 1 4-3 2.2 2.2 0 0 1 4 3z" fill="none" stroke="#f08a00" stroke-width="1.3"/></svg>Fusce accumsan</li>
    <li><svg width="9" height="9" viewBox="0 0 10 10"><path d="M5 9 1 5a2.2 2.2 0 0 1 4-3 2.2 2.2 0 0 1 4 3z" fill="none" stroke="#f08a00" stroke-width="1.3"/></svg>Phasellus dui ante</li>
    <li><svg width="9" height="9" viewBox="0 0 10 10"><path d="M5 9 1 5a2.2 2.2 0 0 1 4-3 2.2 2.2 0 0 1 4 3z" fill="none" stroke="#f08a00" stroke-width="1.3"/></svg>Morbi iaculis fringilla</li>
    <li><svg width="9" height="9" viewBox="0 0 10 10"><path d="M5 9 1 5a2.2 2.2 0 0 1 4-3 2.2 2.2 0 0 1 4 3z" fill="none" stroke="#f08a00" stroke-width="1.3"/></svg>Aliquam ullamcorper</li>
    <li><svg width="9" height="9" viewBox="0 0 10 10"><path d="M5 9 1 5a2.2 2.2 0 0 1 4-3 2.2 2.2 0 0 1 4 3z" fill="none" stroke="#f08a00" stroke-width="1.3"/></svg>Fusce accumsan</li>
    <li><svg width="9" height="9" viewBox="0 0 10 10"><path d="M5 9 1 5a2.2 2.2 0 0 1 4-3 2.2 2.2 0 0 1 4 3z" fill="none" stroke="#f08a00" stroke-width="1.3"/></svg>Phasellus dui ante</li>
    <li><svg width="9" height="9" viewBox="0 0 10 10"><path d="M5 9 1 5a2.2 2.2 0 0 1 4-3 2.2 2.2 0 0 1 4 3z" fill="none" stroke="#f08a00" stroke-width="1.3"/></svg>Morbi iaculis fringilla</li>
    <li><svg width="9" height="9" viewBox="0 0 10 10"><path d="M5 9 1 5a2.2 2.2 0 0 1 4-3 2.2 2.2 0 0 1 4 3z" fill="none" stroke="#f08a00" stroke-width="1.3"/></svg>Aliquam ullamcorper</li>
  </ul>
</aside>

<section class="panel abs" style="left:108px">
  <h2>Photo Gallery</h2>
  <div class="thumb" role="img" aria-label="Couple close together" style="left:17px;top:43px;background:linear-gradient(135deg,#e2b27a,#7a4a30)"></div>
  <div class="thumb" role="img" aria-label="Young couple outdoors" style="left:134px;top:43px;background:linear-gradient(135deg,#8a9a4a,#c46a6a)"></div>
  <div class="thumb" role="img" aria-label="Laughing couple" style="left:17px;top:134px;background:linear-gradient(135deg,#e8c08a,#b07050)"></div>
  <div class="thumb" role="img" aria-label="Smiling couple on white" style="left:134px;top:134px;background:linear-gradient(135deg,#f0ece8,#8a6a5a)"></div>
</section>

<section class="panel abs" style="left:375px">
  <h2>Video Gallery</h2>
  <div class="thumb" role="img" aria-label="Video: couple at a market stall" style="left:17px;top:43px;background:linear-gradient(135deg,#6a5040,#c0803a)"><svg class="play" width="20" height="20" viewBox="0 0 20 20"><circle cx="10" cy="10" r="10" fill="rgba(0,0,0,.6)"/><path d="M8 6l6 4-6 4z" fill="#fff"/></svg></div>
  <div class="thumb" role="img" aria-label="Video: couple at the beach" style="left:134px;top:43px;background:linear-gradient(135deg,#7fd0e8,#d0a080)"><svg class="play" width="20" height="20" viewBox="0 0 20 20"><circle cx="10" cy="10" r="10" fill="rgba(0,0,0,.6)"/><path d="M8 6l6 4-6 4z" fill="#fff"/></svg></div>
  <div class="thumb" role="img" aria-label="Video: friends talking" style="left:17px;top:134px;background:linear-gradient(135deg,#c04030,#d0c0b0)"><svg class="play" width="20" height="20" viewBox="0 0 20 20"><circle cx="10" cy="10" r="10" fill="rgba(0,0,0,.6)"/><path d="M8 6l6 4-6 4z" fill="#fff"/></svg></div>
  <div class="thumb" role="img" aria-label="Video: couple at night" style="left:134px;top:134px;background:linear-gradient(135deg,#3a1a10,#b06a30)"><svg class="play" width="20" height="20" viewBox="0 0 20 20"><circle cx="10" cy="10" r="10" fill="rgba(0,0,0,.6)"/><path d="M8 6l6 4-6 4z" fill="#fff"/></svg></div>
</section>

<section class="panel abs" style="left:642px">
  <h2>Our Blogs</h2>
  <div class="post" style="top:43px">
    <div class="pic" role="img" aria-label="Couple portrait" style="background:linear-gradient(135deg,#f2f2f2,#9a7a6a)"></div>
    <h3>Aliquam molestie, mi et</h3>
    <p>Sed accumsan sollicitudin sapien, sit amet adipiscing turpis gravida ac.... <em>More</em></p>
  </div>
  <div class="post-rule"></div>
  <div class="post" style="top:135px">
    <div class="pic" role="img" aria-label="Couple portrait" style="background:linear-gradient(135deg,#f2f2f2,#8a6050)"></div>
    <h3>Aliquam molestie, mi et</h3>
    <p>Sed accumsan sollicitudin sapien, sit amet adipiscing turpis gravida ac.... <em>More</em></p>
  </div>
</section>

<section class="register abs">
  <label>Register Your Email:</label>
  <div class="field">Enter Email Address</div>
  <div class="go">REGISTER NOW</div>
</section>

<footer class="site-footer abs">
  <nav class="foot-nav">
    <span>Home</span><span class="sep">|</span><span>About Us</span><span class="sep">|</span><span>Services</span><span class="sep">|</span><span>Videos</span><span class="sep">|</span><span>Gallery</span><span class="sep">|</span><span>Contact Us</span>
  </nav>
  <div class="copy">Copyright 2013. <b>Bright Harbor.</b> All Right Reserved.</div>
  <div class="follow">Follow Us:</div>
  <div class="social">
    <i style="background:#3b5b98" aria-label="Social link"></i>
    <i style="background:#2aa8dc" aria-label="Social link"></i>
    <i style="background:#d6443a" aria-label="Social link"></i>
    <i style="background:#3f8fc8" aria-label="Social link"></i>
    <i style="background:#f26a1c" aria-label="Social link"></i>
    <i style="background:#c3221d" aria-label="Social link"></i>
  </div>
</footer>

</body>
</html>
```